PowerPoint template for a tech startup

We need a PowerPoint template with a title slide, text slide, section slide, and thank you slide.
Our application helps engineering teams to be more productive. We would love a design that is slick, sophisticated, and consistent with our brand. (see more at www.velmo.ai or attached files)
By the way (not a requirement), Velmo means lighthouse in Greek.
Also, here is the font we used (not required) - https://glyphvault.net/fonts/league-gothic

• https://glyphvault.net/fonts/league-gothic

```html
<!DOCTYPE html>
<html lang="en">
<head>
<meta charset="utf-8">
<title>Velmo – Presentation Template</title>
<link rel="stylesheet" href="https://fonts.googleapis.com/css2?family=Poppins:wght@400;500;600;700;800&display=swap">
<style>
:root{
  --page:#efeff1;
  --slide:#0b0b0d;
  --accent:#6a4cf5;
  --white:#ffffff;
  --muted:#c9c9cf;
  --dim:#7d7d86;
  --card:#1b1b20;
  --card-line:#3a3a42;
}
*{margin:0;padding:0;box-sizing:border-box}
html,body{width:1200px;height:4057px;overflow:hidden;background:var(--page)}
body{font-family:"Poppins",sans-serif;color:var(--white);position:relative}
.slide{position:absolute;left:68px;width:1064px;height:598px;overflow:hidden;
  background:radial-gradient(ellipse at 50% 110%,#1d1d24 0%,var(--slide) 60%);
  border:1px solid #2a2a2a}
.s1{top:90px}.s2{top:742px}.s3{top:1395px}.s4{top:2047px}.s5{top:2699px}.s6{top:3353px}
.brand{font-weight:700;color:var(--white);letter-spacing:1px;position:absolute}
.brand-corner{right:26px;top:16px;font-size:36px}
.brand-center{left:0;right:0;text-align:center;font-size:78px;top:92px}
.title{position:absolute;left:25px;top:14px;font-size:36px;font-weight:800;color:var(--accent);letter-spacing:.5px}
.footer{position:absolute;left:25px;bottom:12px;font-size:15px;color:var(--white)}
.pagenum{position:absolute;right:24px;bottom:8px;width:28px;height:28px;border-radius:50%;
  background:var(--accent);font-size:12px;display:flex;align-items:center;justify-content:center}
.url{position:absolute;left:0;right:0;text-align:center;font-size:21px;letter-spacing:16px;font-weight:500}
.hero-line{position:absolute;left:0;right:0;text-align:center;font-size:38px;font-weight:700}
.hero-line .hl{color:var(--accent);background:#15121f;padding:0 12px;border-radius:4px}
.hero-sub{position:absolute;left:0;right:0;top:380px;text-align:center;font-size:11.5px;line-height:24px;color:var(--muted)}
.mission-lead{position:absolute;left:25px;top:104px;width:770px;font-size:14px;line-height:32px}
.mission-strong{position:absolute;left:25px;top:222px;font-size:14px;font-weight:600}
.mission-body{position:absolute;left:25px;top:268px;width:530px;font-size:12.5px;line-height:32px;text-align:justify;color:var(--muted)}
.mission-photo{position:absolute;left:560px;top:0;width:504px;height:598px;
  background:radial-gradient(circle at 45% 55%,#2b3a66 0%,#1a2140 35%,#0b0b0d 75%)}
.feature{position:absolute;top:110px;width:330px;text-align:center}
.feature h3{font-size:19px;font-weight:700;line-height:32px;margin-top:22px}
.feature p{font-size:12px;line-height:29px;color:var(--muted);margin-top:10px}
.f1{left:17px}.f2{left:367px}.f3{left:717px}
.art{height:240px;position:relative}
.node{position:absolute;width:58px;text-align:center}
.node .ico{width:36px;height:36px;margin:0 auto;border-radius:6px;background:#16161c;border:1px solid #2e2e36;display:flex;align-items:center;justify-content:center}
.node .lbl{margin-top:4px;font-size:9px;background:#2c2c33;color:var(--muted);padding:2px 0;border-radius:3px}
.api-box{position:absolute;left:90px;top:50px;width:116px;height:86px;border-radius:6px;
  background:linear-gradient(160deg,#56757c,#2c3d44);border:1px solid #6b8a8f;
  font-size:42px;font-weight:600;color:#173036;display:flex;align-items:center;justify-content:center}
.quote-title{position:absolute;left:0;right:0;top:146px;text-align:center;font-size:36px;font-weight:800;color:var(--accent)}
.quote-rule{position:absolute;left:136px;width:792px;top:245px;height:2px;background:var(--accent)}
.quote-mark{position:absolute;left:511px;top:226px;width:42px;height:42px;border-radius:50%;background:var(--accent);
  font-size:32px;font-weight:800;line-height:56px;text-align:center}
.quote-text{position:absolute;left:137px;width:790px;top:290px;font-size:24px;line-height:43px;text-align:center}
.module{position:absolute;top:112px;height:417px;border-radius:10px;background:var(--card);padding:26px 32px}
.m1{left:106px;width:395px}.m2{left:544px;width:388px}
.module h4{font-size:15px;font-weight:700;display:flex;align-items:center;gap:10px}
.module .desc{font-size:10px;line-height:16px;color:var(--dim);margin-top:10px;height:44px}
.module hr{border:0;border-top:1px solid var(--card-line);margin:6px 0 14px}
.checks{display:grid;grid-template-columns:1fr 1fr;row-gap:20px;font-size:9.5px;color:var(--dim)}
.checks span::before{content:"✓";color:var(--accent);margin-right:10px}
.tools{display:flex;flex-wrap:wrap;align-items:baseline;gap:6px 16px;font-size:17px;font-weight:600;margin-top:4px}
.tools small{font-size:9px;color:var(--dim);font-weight:400}
.module-foot{position:absolute;left:32px;right:32px;bottom:32px;display:flex;justify-content:space-between;align-items:center}
.btn{border:1px solid #8a8a92;border-radius:3px;font-size:10px;padding:5px 30px}
.price{font-size:19px;font-weight:700}
.price small{font-size:7px;font-weight:500;color:var(--muted);margin-left:4px}
.thanks{position:absolute;left:0;right:0;top:258px;text-align:center;font-size:80px;font-weight:800;letter-spacing:2px}
</style>
</head>
<body>

<section class="slide s1">
  <div class="brand brand-center">VELMO</div>
  <div class="hero-line" style="top:262px">The <span class="hl">Connected</span></div>
  <div class="hero-line" style="top:310px">Engineering Operations Platform</div>
  <p class="hero-sub">Velmo AI connects the dots between your engineering data sources – ticketing, source control, CI/CD,<br>and more – giving unprecedented visibility and insight into your engineering processes.</p>
  <div class="url" style="top:550px">WWW.VELMO.AI</div>
</section>

<section class="slide s2">
  <div class="mission-photo" role="img" aria-label="Photo of two engineers looking at a tablet in a dark office"></div>
  <h2 class="title">OUR MISSION</h2>
  <div class="brand brand-corner">VELMO</div>
  <p class="mission-lead">Velmo AI is an operational data platform that brings all engineering data in one place to give engineering leaders a single-pane view of their entire software development lifecycle.</p>
  <p class="mission-strong">Velmo AI is bringing unprecedented visibility to engineering operations.</p>
  <p class="mission-body">Engineering stacks have become increasingly fragmented and diverse, making it very hard for engineering leaders to have a firm grasp of their operations. Seemingly simple questions become incredibly non-trivial to answer. We believe that by equipping leaders with the right tool that brings all engineering data in one place, organizations will be able to operate at a whole new level of efficiency. We're always looking for talented individuals who are interested in building the future alongside us.</p>
  <div class="footer">© 2022, Velmo AI, Inc.</div>
  <div class="pagenum">01</div>
</section>

<section class="slide s3">
  <h2 class="title">FEATURES</h2>
  <div class="brand brand-corner">VELMO</div>
  <div class="feature f1">
    <div class="art">
      <svg width="330" height="240" style="position:absolute;left:0;top:0">
        <line x1="120" y1="54" x2="210" y2="54" stroke="#3a3a42"/>
        <line x1="120" y1="164" x2="210" y2="164" stroke="#3a3a42"/>
        <line x1="90" y1="80" x2="90" y2="140" stroke="#3a3a42"/>
        <line x1="240" y1="80" x2="240" y2="140" stroke="#3a3a42"/>
      </svg>
      <div class="node" style="left:61px;top:36px"><div class="ico"><svg width="14" height="14"><rect x="1" y="2" width="12" height="11" fill="none" stroke="#8d78ff" stroke-width="1.5"/><line x1="1" y1="5" x2="13" y2="5" stroke="#8d78ff"/></svg></div><div class="lbl">Planning</div></div>
      <div class="node" style="left:194px;top:36px"><div class="ico" style="color:#8d78ff;font-size:12px">&lt;/&gt;</div><div class="lbl">Development</div></div>
      <div class="node" style="left:61px;top:146px"><div class="ico"><svg width="14" height="14"><rect x="1" y="1" width="12" height="12" fill="none" stroke="#8d78ff" stroke-width="1.5"/><path d="M4 7l2 2 4-4" fill="none" stroke="#8d78ff" stroke-width="1.5"/></svg></div><div class="lbl">Testing</div></div>
      <div class="node" style="left:194px;top:146px"><div class="ico"><svg width="14" height="14"><path d="M3 11L11 3M7 3h4v4" fill="none" stroke="#8d78ff" stroke-width="1.6"/></svg></div><div class="lbl">Production</div></div>
    </div>
    <h3>Visibility from the backlog to production (and beyond!)</h3>
    <p>Velmo collects and presents data from the whole value stream of software engineering, with proper team attribution.</p>
  </div>
  <div class="feature f2">
    <div class="art">
      <svg width="330" height="240" style="position:absolute;left:0;top:0" role="img" aria-label="Rising bar chart">
        <defs><linearGradient id="bar" x1="0" y1="0" x2="0" y2="1"><stop offset="0" stop-color="#9b8fc8"/><stop offset="1" stop-color="#4a4858"/></linearGradient></defs>
        <rect x="30" y="185" width="24" height="20" fill="url(#bar)"/>
        <rect x="62" y="160" width="24" height="45" fill="url(#bar)"/>
        <rect x="94" y="126" width="24" height="79" fill="url(#bar)"/>
        <rect x="126" y="100" width="24" height="105" fill="url(#bar)"/>
        <rect x="158" y="72" width="24" height="133" fill="url(#bar)"/>
        <rect x="190" y="50" width="24" height="155" fill="url(#bar)"/>
        <rect x="222" y="30" width="24" height="175" fill="url(#bar)"/>
        <polyline points="42,165 74,130 106,104 138,110 170,70 202,60" fill="none" stroke="#c34a4a" stroke-width="1.5"/>
      </svg>
    </div>
    <h3>100+ metrics and industry benchmarks</h3>
    <p>Velmo leverages the latest research in DevOps (e.g. FLOW) to deliver meaningful metrics, insights, and industry benchmarks.</p>
  </div>
  <div class="feature f3">
    <div class="art">
      <svg width="330" height="240" style="position:absolute;left:0;top:0">
        <path d="M30 20 V110 H70 M250 20 V110 H220 M150 160 V200" fill="none" stroke="#2e2e36"/>
      </svg>
      <div class="api-box">API</div>
    </div>
    <h3>Configurable &amp; customizable APIs</h3>
    <p>Velmo is an extensible API-based platform that allows you to send and inspect your data, and build your own reports.</p>
  </div>
  <div class="footer">© 2022, Velmo AI, Inc.</div>
  <div class="pagenum">02</div>
</section>

<section class="slide s4">
  <div class="brand brand-corner">VELMO</div>
  <h2 class="quote-title">HERE'S WHY PEOPLE LOVE VELMO</h2>
  <div class="quote-rule"></div>
  <div class="quote-mark">“</div>
  <p class="quote-text">"Getting visibility into engineering operations and pipelines is effortless with Velmo. Every company I've worked at builds this kind of tooling over &amp; over again with ad hos scripts and lots of manual effort."</p>
  <div class="footer">© 2022, Velmo AI, Inc.</div>
  <div class="pagenum">03</div>
</section>

<section class="slide s5">
  <h2 class="title">PRODUCTIVITY MODULES</h2>
  <div class="brand brand-corner">VELMO</div>
  <div class="module m1">
    <h4><svg width="14" height="12"><circle cx="3" cy="6" r="2" fill="#fff"/><circle cx="11" cy="2" r="2" fill="#fff"/><circle cx="11" cy="10" r="2" fill="#fff"/><path d="M3 6L11 2M3 6L11 10" stroke="#fff"/></svg>Value Stream Analysis</h4>
    <p class="desc">Get visibility into the velocity and quality of your changes as they move to Production. Includes FLOW metrics!</p>
    <hr>
    <div class="checks"><span>Deployment Frequency</span><span>Lead Time for Changes</span><span>Change Failure Rate</span><span>Time to Restore Service</span></div>
    <hr style="margin-top:22px">
    <div class="tools"><span>Ovrabuild</span><span>Pingarro</span><span>Zentoloop</span><span>Oncallo</span><small>+ many more</small></div>
    <div class="module-foot"><span class="btn">Contact Us</span><span class="price">$10<small>USD / month / user</small></span></div>
  </div>
  <div class="module m2">
    <h4><svg width="14" height="14"><circle cx="7" cy="7" r="5" fill="none" stroke="#fff" stroke-width="2.5" stroke-dasharray="3 2"/><circle cx="7" cy="7" r="2" fill="#fff"/></svg>Engineering Productivity</h4>
    <p class="desc">Get Visibility into your organization and processes. Plan better. Align your teams. Improve your productivity.</p>
    <hr>
    <div class="checks"><span>Task and PR Cycle Time</span><span>Planned vs Unplanned Work</span><span>Epic Progress</span><span>Onboarding Metrics</span></div>
    <hr style="margin-top:22px">
    <div class="tools"><span>Taskvarn</span><span>Pullvane</span><span>Mergetide</span><span>Codemoor</span><small>+ many more</small></div>
    <div class="module-foot"><span class="btn">Contact Us</span><span class="price">$10<small>USD / month / user</small></span></div>
  </div>
  <div class="footer">© 2022, Velmo AI, Inc.</div>
  <div class="pagenum">04</div>
</section>

<section class="slide s6">
  <div class="brand brand-center" style="top:64px">VELMO</div>
  <div class="thanks">THANK YOU</div>
  <div class="url" style="top:405px">WWW.VELMO.AI</div>
</section>

</body>
</html>
```